Flyer for the Lumen 2025 Conference

I am looking to produce a flyer for our upcoming conference, Lumen 2025. This is an annual conference that we plan to publicize on social media. The ideal designer will create a flyer that is eye-catching and effectively communicates the key information. Please see attached our logo, speaker photo, and flyer content.

Target Market(s)

All demographics

Industry/Entity Type

Christian

Font styles to use
Sans Serif

Requirements
Should not have
• Cross, church

```html
<!DOCTYPE html>
<html lang="en">
<head>
<meta charset="utf-8">
<title>Lumen 2025 Conference</title>
<link rel="stylesheet" href="https://fonts.googleapis.com/css2?family=Anton&family=Montserrat:wght@300;400;700;800&family=Poppins:wght@400;700;800&display=swap">
<style>
:root{
  --orange:#f7941d;
  --orange-light:#fbb03b;
  --navy:#0d2474;
  --blue:#0a7be8;
  --paper:#f3f3f3;
  --ink:#1a1a1a;
  --white:#ffffff;
}
*{margin:0;padding:0;box-sizing:border-box}
html,body{width:927px;height:1200px;overflow:hidden;background:var(--paper)}
.flyer{position:relative;width:927px;height:1200px;overflow:hidden;background:var(--paper);font-family:"Montserrat",sans-serif;color:var(--ink)}
.backdrop{position:absolute;inset:0}
.stage-photo{position:absolute;left:653px;top:0;width:274px;height:550px;background:radial-gradient(ellipse at 40% 35%,#9a9a9a 0%,#c9c9c9 45%,rgba(243,243,243,0) 80%)}
.speaker-photo{position:absolute;left:0;top:380px;width:535px;height:820px;background:linear-gradient(180deg,rgba(30,80,190,0) 0%,#1d5fd0 25%,#1546a8 60%,#0e2f7a 100%);border-radius:220px 220px 0 0}
.topic{position:absolute;left:68px;top:55px;font-size:25px;line-height:33px;font-weight:300}
.topic .label{color:var(--orange);display:block;font-size:23px}
.topic b{font-weight:400}
.topic-rule{position:absolute;left:69px;top:159px;width:1px;height:385px;background:var(--ink)}
.brand{position:absolute;left:367px;top:58px;width:200px;text-align:center}
.brand .name{font-family:"Montserrat",sans-serif;font-weight:700;font-size:36px;color:var(--navy);letter-spacing:1px;line-height:40px}
.brand .tagline{font-size:9px;color:var(--orange);letter-spacing:.5px;font-weight:400}
.title{position:absolute;left:277px;top:130px}
.subtitle{position:absolute;left:285px;top:472px;width:364px}
.subtitle .lead{font-family:"Poppins",sans-serif;font-weight:800;font-size:49px;color:var(--blue);line-height:56px;white-space:nowrap}
.subtitle .tail{font-family:"Montserrat",sans-serif;font-weight:300;font-size:52px;color:var(--navy);line-height:58px;letter-spacing:.5px}
.month{position:absolute;left:464px;top:711px;width:34px;height:193px;display:flex;align-items:center;justify-content:center}
.month span{transform:rotate(-90deg);font-family:"Poppins",sans-serif;font-weight:800;font-size:33px;color:var(--blue);white-space:nowrap}
.sessions{position:absolute;left:508px;top:710px;width:350px;list-style:none}
.session{display:flex;height:54px;margin-bottom:8.5px;background:var(--navy);border-radius:27px;overflow:hidden}
.session .day{width:132px;padding-left:20px;font-family:"Poppins",sans-serif;font-weight:800;font-size:40px;color:var(--orange-light);line-height:54px}
.session .day sup{font-size:24px;vertical-align:14px}
.session .time{flex:1;background:var(--blue);border-radius:27px;padding:6px 0 0 28px;color:var(--white);font-family:"Poppins",sans-serif;line-height:21px}
.session .time .weekday{font-size:18px;font-weight:400;display:block}
.session .time .hours{font-size:18px;font-weight:700;display:block}
.rule{position:absolute;left:524px;width:334px;height:1px;background:var(--ink)}
.venue{position:absolute;left:524px;top:936px;font-family:"Poppins",sans-serif;font-weight:700;font-size:16.5px;color:var(--orange)}
.address{position:absolute;left:526px;top:969px;display:flex;align-items:center;gap:11px}
.address .pin{width:41px;height:39px;border:2px solid var(--orange);border-radius:14px;background:var(--navy);display:flex;align-items:center;justify-content:center}
.address p{font-size:17px;line-height:19px;letter-spacing:1px;font-weight:400}
.app-note{position:absolute;left:527px;top:1044px;font-family:"Poppins",sans-serif;font-size:20px;line-height:22px}
.app-note .hl-orange{color:var(--orange);font-weight:700}
.app-note .hl-blue{color:var(--blue);font-weight:700}
.store-badge{position:absolute;left:770px;width:86px;height:28px;background:#0b0b0b;border-radius:5px}
.speaker-card{position:absolute;left:0;top:1010px;width:311px;height:113px;background:var(--navy);border-radius:0 26px 26px 0;padding:16px 0 0 68px;opacity:.95}
.speaker-card .role{font-size:26px;font-weight:300;color:var(--orange);line-height:28px}
.speaker-card .name{font-family:"Poppins",sans-serif;font-weight:800;font-size:28px;line-height:32px;color:var(--white)}
.contact-bar{position:absolute;left:0;top:1134px;width:927px;height:30px;background:linear-gradient(90deg,var(--blue),var(--navy));display:flex;align-items:center;color:var(--white);font-size:20px;letter-spacing:.5px}
.contact-bar .item{position:absolute;display:flex;align-items:center;gap:8px}
</style>
</head>
<body>
<main class="flyer">
  <svg class="backdrop" width="927" height="1200" viewBox="0 0 927 1200" aria-hidden="true">
    <polygon points="0,38 538,1200 0,1200" fill="#f7941d"/>
    <polygon points="0,38 300,685 0,685" fill="#fbb03b" opacity=".35"/>
  </svg>

  <div class="stage-photo" role="img" aria-label="Soft grey photo of a stage microphone with blurred lights"></div>
  <div class="speaker-photo" role="img" aria-label="Photo of the speaker seated, wearing a bright blue suit"></div>

  <p class="topic"><span class="label">Topic:</span>The <b>Voice</b><br>Of The <b>Lord</b></p>
  <div class="topic-rule"></div>

  <div class="brand">
    <div class="name">VERAH</div>
    <div class="tagline">A LIGHT TO EVERY SHORE</div>
  </div>

  <svg class="title" width="380" height="320" viewBox="0 0 380 320" aria-label="Lumen 2025">
    <text x="0" y="134" font-family="Anton, sans-serif" font-size="172" fill="#f7941d" textLength="374" lengthAdjust="spacingAndGlyphs">LUMEN</text>
    <text x="6" y="312" font-family="Anton, sans-serif" font-size="222" fill="#0d2474" textLength="366" lengthAdjust="spacingAndGlyphs">2025</text>
  </svg>

  <div class="subtitle">
    <div class="lead">A PROPHETIC</div>
    <div class="tail">CONFERENCE</div>
  </div>

  <div class="month"><span>December</span></div>
  <ul class="sessions">
    <li class="session"><span class="day">26<sup>th</sup></span><span class="time"><span class="weekday">Friday</span><span class="hours">6:30PM - 9:00PM</span></span></li>
    <li class="session"><span class="day">27<sup>th</sup></span><span class="time"><span class="weekday">Saturday</span><span class="hours">5:30PM - 8:00PM</span></span></li>
    <li class="session"><span class="day">28<sup>th</sup></span><span class="time"><span class="weekday">Sunday</span><span class="hours">4:30PM - 7:00PM</span></span></li>
  </ul>

  <div class="rule" style="top:915px"></div>
  <p class="venue">The Riverside Performing Arts Center</p>
  <div class="address">
    <span class="pin">
      <svg width="20" height="24" viewBox="0 0 20 24" aria-hidden="true"><path d="M10 1a8 8 0 0 0-8 8c0 6 8 14 8 14s8-8 8-14a8 8 0 0 0-8-8z" fill="#fff"/><circle cx="10" cy="9" r="3" fill="#0d2474"/></svg>
    </span>
    <p>238 Harbor Mill Road<br>Easton, Maine 04000</p>
  </div>
  <div class="rule" style="top:1032px"></div>

  <p class="app-note"><span class="hl-orange">Download</span> the<br><span class="hl-blue">VERAH App</span> to stay<br>updated on the event</p>
  <div class="store-badge" style="top:1046px" aria-label="App store badge"></div>
  <div class="store-badge" style="top:1082px" aria-label="App store badge"></div>

  <div class="speaker-card">
    <div class="role">SPEAKER:</div>
    <div class="name">PROPHET<br>SAMUEL OKORO</div>
  </div>

  <footer class="contact-bar">
    <span class="item" style="left:69px">
      <svg width="20" height="20" viewBox="0 0 20 20" aria-hidden="true"><g fill="none" stroke="#fff" stroke-width="2"><circle cx="10" cy="10" r="8.5"/><ellipse cx="10" cy="10" rx="3.5" ry="8.5"/><path d="M1.5 10h17"/></g></svg>
      www.verah.org
    </span>
    <span class="item" style="left:359px">
      <svg width="18" height="18" viewBox="0 0 24 24" aria-hidden="true"><path fill="#fff" d="M6.6 10.8a15.1 15.1 0 0 0 6.6 6.6l2.2-2.2a1 1 0 0 1 1-.25 11.4 11.4 0 0 0 3.6.57 1 1 0 0 1 1 1V20a1 1 0 0 1-1 1A17 17 0 0 1 3 4a1 1 0 0 1 1-1h3.5a1 1 0 0 1 1 1c0 1.25.2 2.45.57 3.57a1 1 0 0 1-.25 1z"/></svg>
      207 555 0142
    </span>
    <span class="item" style="left:620px">
      <svg width="20" height="16" viewBox="0 0 20 16" aria-hidden="true"><rect x="1" y="1" width="18" height="14" rx="2" fill="#fff"/><path d="M2 3l8 6 8-6" fill="none" stroke="#0d2474" stroke-width="2"/></svg>
      contact@verah.org
    </span>
  </footer>
</main>
</body>
</html>
```